A Brochure to sell LED Downlights to clients

I am starting a campaign on google for LED down lights the link to the landing page can be found at brinholt.com.au/led .

When the client send a contact request i want to be able to send back a brochure of a picture of each light (Approx 6 - 8 types) and have a few sentences on each light and price brake down.

'Quarnel Ostrava 9w LED'

**Information**

1-10 lights $49
11-20 lights $45
21 - 40 lights $42
40 and over $40

EACH LIGHT:

Hi,

This is very good.

I
But,

Each light will have its own price.

Can i get it made like this;

Picture - Spec - Pricing in a table style please? - i like the layout it just need to suit the tables under:

picture - Brand - Price 1-10
Model - Price 11-20
Watts - Price 21-21
lumen - price 30- 40
Warranty = price 40+

Model - Price 11-20
Watts - Price 21-21
lumen - price 30- 40
Warranty = price 40+

Model - Price 11-20
Watts - Price 21-21
lumen - price 30- 40
Warranty = price 40+

and so on....

I want it to be on Microsoft Word so i can easily chop and edit the prices and images also. (So i can print to PDF)

For more information see my website to seek inspiration. I have a zip file of my logo for actual creation and should be also to source pictures of the lights when finalising the design.

brinholt.com.au

Thanks

Added 2 x additional Dimmers please see zip file, same layout/pricing as the downlights

Target Market(s)

Homeowners/commercial business owners

Industry/Entity Type

Electric Company

Font styles to use
Sans Serif

Colors
86cfc6
ffffff
000000

Requirements
Must have
• Professional looking, Colours to the theme of my logo/website
Nice to have
• An awesome design that sells it's self!!!!!!!
• My Logo font is 'Radikil" it would be nice to follow that theme if it doesn't look good i am open to have a nice legible font for the copy.
Should not have
• Cheesy light globes or images

```html
<!DOCTYPE html>
<html lang="en">
<head>
<meta charset="utf-8">
<title>Brinholt Electrical – LED Downlights Catalog</title>
<link href="https://fonts.googleapis.com/css2?family=Fredoka:wght@500;600&family=Didact+Gothic&family=Questrial&display=swap" rel="stylesheet">
<style>
  :root{
    --teal:#14a89d;
    --teal-deep:#0f9e92;
    --teal-soft:#86cfc6;
    --charcoal:#3d3d3d;
    --stage:#c9c9c9;
    --paper:#ffffff;
    --ink:#333333;
  }
  *{box-sizing:border-box;margin:0;padding:0}
  html,body{width:1200px;height:2980px;overflow:hidden}
  body{background:var(--stage);position:relative;font-family:"Didact Gothic",sans-serif;color:var(--ink)}
  .page{position:absolute;overflow:hidden;box-shadow:6px 8px 14px rgba(0,0,0,.35)}

  /* Cover */
  .cover{left:290px;top:115px;width:622px;height:879px;background:var(--paper)}
  .cover-photo{position:absolute;left:0;top:0;width:622px;height:694px;
    background:linear-gradient(180deg,#ffffff 0%,#fbf8f3 22%,#efe6d9 45%,#d9c9b3 62%,#b7a58c 78%,#8c7c68 100%)}
  .cover-title{position:absolute;left:0;top:42px;width:100%;text-align:center}
  .cover-title .big{font-family:"Fredoka",sans-serif;font-weight:600;font-size:68px;letter-spacing:2px;color:var(--teal);line-height:1}
  .cover-title .boxed{display:inline-block;margin-top:6px;padding:2px 8px;border:2px solid #555;font-family:"Questrial",sans-serif;font-size:52px;letter-spacing:1px;color:#333;line-height:1.05;background:rgba(255,255,255,.6)}
  .cover-band{position:absolute;left:0;top:694px;width:100%;height:12px;background:var(--teal)}
  .cover-foot{position:absolute;left:0;top:706px;width:100%;height:173px;background:var(--charcoal)}
  .brand{font-family:"Questrial",sans-serif;color:var(--paper);line-height:1}
  .cover-foot .brand{position:absolute;left:22px;top:66px}
  .brand .name{font-size:44px;display:block}
  .brand .trade{font-size:16px;letter-spacing:3px;display:block;margin-top:4px;padding-left:46px}
  .cover-foot .url{position:absolute;right:24px;bottom:22px;font-family:"Questrial",sans-serif;font-size:24px;color:var(--paper)}

  /* Catalog page */
  .range{left:278px;top:1063px;width:640px;height:900px;background:linear-gradient(180deg,#f7f7f7 0%,#e6e6e6 100%)}
  .range-title{position:absolute;left:0;top:26px;width:100%;text-align:center;font-family:"Fredoka",sans-serif;font-weight:600;font-size:38px;line-height:1.2;color:var(--teal);letter-spacing:.5px}
  .spec-table{position:absolute;left:24px;top:132px;width:596px;height:562px;border:3px solid var(--teal);border-radius:18px;overflow:hidden;background:var(--paper)}
  .spec-head{display:flex;height:32px;background:var(--teal);color:var(--paper);font-size:17px;align-items:center}
  .spec-head .c-spec{width:454px;text-align:center;padding-left:160px}
  .spec-head .c-price{width:142px;text-align:center}
  .spec-row{display:flex;height:132px;border-top:3px solid var(--teal)}
  .spec-head + .spec-row{border-top:0}
  .cell-photo{width:160px;border-right:3px solid var(--teal);display:flex;align-items:center;justify-content:center}
  .light-photo{width:92px;height:92px;border-radius:50%;background:radial-gradient(circle at 40% 38%,#ffffff 0%,#d8d8d8 55%,#8a8a8a 100%)}
  .cell-spec{width:294px;border-right:3px solid var(--teal);padding:14px 0 0 14px}
  .cell-spec h3{font-family:"Questrial",sans-serif;font-weight:400;font-size:19px;color:var(--teal);margin-bottom:6px}
  .cell-spec ul{list-style:none}
  .cell-spec li{font-size:12.5px;line-height:19px;display:flex;align-items:center;gap:8px;color:#333;white-space:nowrap}
  .cell-spec li svg{flex:none}
  .cell-price{flex:1;display:flex;align-items:center;justify-content:center;font-family:"Fredoka",sans-serif;font-weight:600;font-size:30px;color:var(--teal)}

  .tier-box{position:absolute;left:28px;top:733px;width:590px;height:123px;background:var(--charcoal);border:3px solid var(--teal);border-radius:18px;color:var(--paper);font-family:"Questrial",sans-serif;font-size:21px}
  .tier-label{position:absolute;left:190px;top:718px;width:260px;height:30px;background:var(--teal);color:var(--paper);font-family:"Questrial",sans-serif;font-size:18px;text-align:center;line-height:30px;z-index:2;white-space:nowrap}
  .tier{position:absolute;white-space:nowrap;line-height:26px}
  .tier .amt{color:var(--teal-soft);margin-left:6px}
  .tier-a{left:36px;top:36px}
  .tier-b{left:36px;top:68px}
  .tier-c{left:360px;top:36px}
  .tier-d{left:360px;top:68px}
  .range .url{position:absolute;right:24px;top:868px;font-size:16px;color:#444}

  /* Back cover */
  .back{left:290px;top:2027px;width:622px;height:874px;background:var(--teal)}
  .back-strip{position:absolute;left:0;top:0;width:100%;height:12px;background:#7a7a7a}
  .back-photo{position:absolute;left:0;top:12px;width:100%;height:862px;
    background:radial-gradient(ellipse at 50% 30%,rgba(255,255,255,.12) 0%,rgba(255,255,255,0) 55%),linear-gradient(180deg,#17ada1 0%,#12a296 50%,#0e988c 100%)}
  .back .brand{position:absolute;left:0;top:318px;width:100%;text-align:center}
  .back .brand .trade{padding-left:0}
  .back .url{position:absolute;left:0;bottom:34px;width:100%;text-align:center;font-family:"Questrial",sans-serif;font-size:24px;color:var(--paper)}
</style>
</head>
<body>

<section class="page cover">
  <div class="cover-photo" role="img" aria-label="Photo of a shop interior lit by recessed LED downlights"></div>
  <div class="cover-title">
    <div class="big">PRODUCT</div>
    <div class="boxed">CATALOG</div>
  </div>
  <div class="cover-band"></div>
  <div class="cover-foot">
    <div class="brand"><span class="name">brinholt</span><span class="trade">Electrical</span></div>
    <div class="url">brinholt.com.au</div>
  </div>
</section>

<section class="page range">
  <h1 class="range-title">CHOOSE YOUR STYLE OF<br>LED DOWNLIGHTS</h1>

  <div class="spec-table">
    <div class="spec-head"><div class="c-spec">Specification</div><div class="c-price">Price</div></div>

    <div class="spec-row">
      <div class="cell-photo"><div class="light-photo" role="img" aria-label="Photo of a white LED downlight"></div></div>
      <div class="cell-spec">
        <h3>Lorem ipsum dolor</h3>
        <ul>
          <li><svg width="11" height="11"><circle cx="5.5" cy="5.5" r="5.5" fill="#14a89d"/></svg>Save 80% on your energy bills with LEDs</li>
          <li><svg width="11" height="11"><circle cx="5.5" cy="5.5" r="5.5" fill="#14a89d"/></svg>50,000 hours of life</li>
          <li><svg width="11" height="11"><circle cx="5.5" cy="5.5" r="5.5" fill="#14a89d"/></svg>Up to 7 years manufacturer's warranty</li>
          <li><svg width="11" height="11"><circle cx="5.5" cy="5.5" r="5.5" fill="#14a89d"/></svg>Brighter than halogen downlights</li>
        </ul>
      </div>
      <div class="cell-price">000$</div>
    </div>

    <div class="spec-row">
      <div class="cell-photo"><div class="light-photo" role="img" aria-label="Photo of a white LED downlight with driver"></div></div>
      <div class="cell-spec">
        <h3>Lorem ipsum dolor</h3>
        <ul>
          <li><svg width="11" height="11"><circle cx="5.5" cy="5.5" r="5.5" fill="#14a89d"/></svg>Save 80% on your energy bills with LEDs</li>
          <li><svg width="11" height="11"><circle cx="5.5" cy="5.5" r="5.5" fill="#14a89d"/></svg>50,000 hours of life</li>
          <li><svg width="11" height="11"><circle cx="5.5" cy="5.5" r="5.5" fill="#14a89d"/></svg>Up to 7 years manufacturer's warranty</li>
          <li><svg width="11" height="11"><circle cx="5.5" cy="5.5" r="5.5" fill="#14a89d"/></svg>Brighter than halogen downlights</li>
        </ul>
      </div>
      <div class="cell-price">000$</div>
    </div>

    <div class="spec-row">
      <div class="cell-photo"><div class="light-photo" role="img" aria-label="Photo of a black LED downlight with driver"></div></div>
      <div class="cell-spec">
        <h3>Lorem ipsum dolor</h3>
        <ul>
          <li><svg width="11" height="11"><circle cx="5.5" cy="5.5" r="5.5" fill="#14a89d"/></svg>Save 80% on your energy bills with LEDs</li>
          <li><svg width="11" height="11"><circle cx="5.5" cy="5.5" r="5.5" fill="#14a89d"/></svg>50,000 hours of life</li>
          <li><svg width="11" height="11"><circle cx="5.5" cy="5.5" r="5.5" fill="#14a89d"/></svg>Up to 7 years manufacturer's warranty</li>
          <li><svg width="11" height="11"><circle cx="5.5" cy="5.5" r="5.5" fill="#14a89d"/></svg>Brighter than halogen downlights</li>
        </ul>
      </div>
      <div class="cell-price">000$</div>
    </div>

    <div class="spec-row">
      <div class="cell-photo"><div class="light-photo" role="img" aria-label="Photo of a silver finned LED downlight"></div></div>
      <div class="cell-spec">
        <h3>Lorem ipsum dolor</h3>
        <ul>
          <li><svg width="11" height="11"><circle cx="5.5" cy="5.5" r="5.5" fill="#14a89d"/></svg>Save 80% on your energy bills with LEDs</li>
          <li><svg width="11" height="11"><circle cx="5.5" cy="5.5" r="5.5" fill="#14a89d"/></svg>50,000 hours of life</li>
          <li><svg width="11" height="11"><circle cx="5.5" cy="5.5" r="5.5" fill="#14a89d"/></svg>Up to 7 years manufacturer's warranty</li>
          <li><svg width="11" height="11"><circle cx="5.5" cy="5.5" r="5.5" fill="#14a89d"/></svg>Brighter than halogen downlights</li>
        </ul>
      </div>
      <div class="cell-price">000$</div>
    </div>
  </div>

  <div class="tier-label">Quarnel Ostrava 9w LED</div>
  <div class="tier-box">
    <div class="tier tier-a">1-10......lights :<span class="amt">$49</span></div>
    <div class="tier tier-b">11-20...lights :<span class="amt">$45</span></div>
    <div class="tier tier-c">21-40...lights :<span class="amt">$42</span></div>
    <div class="tier tier-d">40 and over :<span class="amt">$40</span></div>
  </div>

  <div class="url">www.brinholt.com.au</div>
</section>

<section class="page back">
  <div class="back-strip"></div>
  <div class="back-photo" role="img" aria-label="Teal-tinted photo of a bedroom lit by downlights"></div>
  <div class="brand"><span class="name">brinholt</span><span class="trade">Electrical</span></div>
  <div class="url">www.brinholt.com.au</div>
</section>

</body>
</html>
```